Gearhead Rally 5, The fifth annual Gearhead Rally motorcycle event, www.gearheadrally.example

We need an event poster that can be used in print and on the web to promote our event. Files for the poster should be modifiable to add additional information as it becomes available. The Gearhead Rally is a gathering for Vintage, Classic and Cafe' Racer motorcycles and their riders, Rockers and Mods. The event date is Saturday, July 26, 2014, rain or shine, from 9:00 AM to 6:00 PM EDT at Maplewick Park, 217 North Birch Avenue, Pittston, PA 18651 USA. Friday July 25 Meet and Greet from 7:00 PM to close at Hadley's Hideaway, Pittston, PA. Early Birds' Brunch, Sunday, July 27, 7:00 to 10:00 AM, location tba. Optional Group Ride Saturday from 10:00 AM to Noon. Tarvex 450 Custom Cafe' Motorcycle Raffle, Contests, Trophies and Cash Prizes for Pin-up Girl, Coolest Cafe' Racer Motorcycle, Coolest Mod Scooter, Peoples Choice Motorcycle, and More! Live music by the one and only legendary KLTV, "Slim Jim" Varga and more tba. Brought to you by Wyland Throttlers, www.social.example/wylandthrottlers?ref=hl, Bixby and Moss/Moss Rascals, www.bixbyandmoss.example. Partial Proceeds to benefit the UFWL and The Valley Rescue Volunteers Society. More information and advance tickets available at www.gearheadrally.example
Uploaded files include: Wyland Throttlers Logo, Moss Rascal's Logo, stock vintage image, two images from 2014 event, and a photo of the bike to be raffled (better image in the works.

Thank you to all who participated in our competition.  We received excellent work from you all, and the hard part for us is having to choose.  Our decision will be made today.

```html
<!DOCTYPE html>
<html lang="en">
<head>
<meta charset="utf-8">
<title>The Fifth Annual Gearhead Rally – July 26 2014</title>
<link rel="stylesheet" href="https://fonts.googleapis.com/css2?family=Montserrat:wght@500;600&family=Oswald:wght@400;500&display=swap">
<style>
  :root {
    --ink: #000000;
    --paper: #ffffff;
    --slate: #58595b;
    --photo-light: #b9b9b9;
    --photo-mid: #6e6e6e;
    --photo-dark: #1c1c1c;
  }
  html, body {
    margin: 0;
    padding: 0;
    width: 1200px;
    height: 1000px;
    overflow: hidden;
    background: var(--ink);
  }
  .poster {
    display: block;
    width: 1200px;
    height: 1000px;
  }
  .poster__backdrop { fill: var(--ink); }
  .headline-kicker {
    font-family: "Montserrat", sans-serif;
    font-weight: 600;
    font-size: 134px;
    fill: var(--slate);
  }
  .headline-name,
  .headline-word {
    font-family: "Montserrat", sans-serif;
    font-weight: 600;
    fill: var(--paper);
  }
  .headline-name { font-size: 262px; }
  .headline-word { font-size: 510px; }
  .tagline-band { fill: var(--ink); }
  .tagline {
    font-family: "Oswald", sans-serif;
    font-weight: 500;
    font-size: 32px;
    letter-spacing: 3px;
    fill: var(--paper);
  }
  .event-date {
    font-family: "Montserrat", sans-serif;
    font-weight: 600;
    font-size: 74px;
    fill: var(--paper);
  }
  .event-details {
    font-family: "Oswald", sans-serif;
    font-weight: 400;
    font-size: 19px;
    letter-spacing: 1.5px;
    fill: var(--paper);
  }
</style>
</head>
<body>
<svg class="poster" viewBox="0 0 1200 1000" xmlns="http://www.w3.org/2000/svg">
  <defs>
    <linearGradient id="bike-tones" x1="0" y1="0" x2="1" y2="1">
      <stop offset="0" stop-color="var(--photo-mid)"/>
      <stop offset="0.35" stop-color="var(--photo-light)"/>
      <stop offset="0.7" stop-color="var(--photo-mid)"/>
      <stop offset="1" stop-color="var(--photo-dark)"/>
    </linearGradient>
  </defs>

  <rect class="poster__backdrop" width="1200" height="1000"/>

  <text class="headline-kicker" x="38" y="108" textLength="1142" lengthAdjust="spacingAndGlyphs">THE FIFTH ANNUAL</text>
  <text class="headline-name" x="38" y="320" textLength="1144" lengthAdjust="spacingAndGlyphs">GEARHEAD</text>
  <text class="headline-word" x="36" y="705" textLength="1144" lengthAdjust="spacingAndGlyphs">RALLY</text>

  <path class="bike-photo" fill="url(#bike-tones)" role="img"
        aria-label="Halftone black and white photo of a café racer motorcycle with a polished fuel tank"
        d="M40 940 L70 820 L200 700 L250 620 L330 600 L420 610 L520 650 L640 690 L780 700 L900 655 L990 690 L1000 940 Z"/>

  <g class="tagline-group" transform="translate(22 622) rotate(-11.6)">
    <rect class="tagline-band" x="-8" y="-36" width="1180" height="46"/>
    <text class="tagline" x="0" y="0" textLength="1160" lengthAdjust="spacingAndGlyphs">VINTAGE, CLASSIC AND CAFÉ RACER MOTORCYCLES AND THEIR RIDERS</text>
  </g>

  <text class="event-date" x="700" y="786" textLength="476" lengthAdjust="spacingAndGlyphs">JULY 26 2014</text>

  <text class="event-details" x="20" y="978" textLength="1160" lengthAdjust="spacingAndGlyphs">RAIN OR SHINE. 09:00 AM TO 06:00 PM EDT AT MAPLEWICK PARK, 217 NORTH BIRCH AVENUE, PITTSTON, PA 18651 USA</text>
</svg>
</body>
</html>
```